1876 Basins & Spouts Business Card

I'm wanting to get a business card designed. Our business is 1876 Basins & Spouts
Details for the card:

1876 Basins & Spouts
Name: Harold Vesk
Email: harold@1876basinsandspouts.com.au
Website: www.1876basinsandspouts.com.au
Mobile: 0438 260 947
Phone: 02 7481 3926

Font of Basins & Spouts is called Snell Roundhand. Not sue what font logo text is.

I'm thinking two sided but it doesn't have to be.

```html
<!DOCTYPE html>
<html lang="en">
<head>
<meta charset="utf-8">
<title>1876 Basins &amp; Spouts Business Card</title>
<link href="https://fonts.googleapis.com/css2?family=Roboto:wght@300;400;700&display=swap" rel="stylesheet">
<style>
  :root {
    --page: #d9d9d9;
    --card-light: #ffffff;
    --card-dark: #141414;
    --ink: #1a1a1a;
    --ink-soft: #555555;
    --paper-text: #f2f2f2;
    --rule: #9a9a9a;
  }
  * { box-sizing: border-box; margin: 0; padding: 0; }
  html, body { width: 1200px; height: 840px; overflow: hidden; }
  body {
    background: var(--page);
    font-family: "Roboto", Arial, sans-serif;
    display: flex;
    align-items: center;
    justify-content: center;
    gap: 60px;
  }
  .card {
    width: 520px;
    height: 300px;
    position: relative;
    box-shadow: 0 6px 18px rgba(0,0,0,0.18);
  }
  .card--front {
    background: var(--card-light);
    color: var(--ink);
    display: flex;
    flex-direction: column;
    align-items: center;
    justify-content: center;
    gap: 26px;
  }
  .brand {
    display: flex;
    align-items: center;
    gap: 14px;
  }
  .brand__mark {
    width: 44px;
    height: 44px;
    border-radius: 50%;
    border: 2px solid var(--ink);
    flex: none;
  }
  .brand__text { display: flex; flex-direction: column; gap: 6px; }
  .brand__name {
    font-size: 28px;
    font-weight: 400;
    letter-spacing: 0.5px;
    color: var(--ink);
  }
  .brand__tagline {
    font-size: 9px;
    font-weight: 300;
    color: var(--ink-soft);
    letter-spacing: 0.3px;
  }
  .front__web {
    font-size: 12px;
    letter-spacing: 2.4px;
    color: var(--ink);
  }
  .card--back {
    background: var(--card-dark);
    color: var(--paper-text);
    display: flex;
    align-items: center;
    padding-left: 52px;
  }
  .holder {
    font-size: 22px;
    font-weight: 700;
    width: 170px;
  }
  .divider {
    width: 1px;
    height: 110px;
    background: linear-gradient(to bottom, transparent, var(--rule), transparent);
    margin-right: 22px;
  }
  .contacts { list-style: none; display: flex; flex-direction: column; gap: 5px; }
  .contacts li {
    display: flex;
    align-items: center;
    gap: 9px;
    font-size: 13px;
    font-weight: 300;
    white-space: nowrap;
  }
  .contacts svg { width: 12px; height: 12px; flex: none; fill: var(--paper-text); }
</style>
</head>
<body>
  <section class="card card--front">
    <div class="brand">
      <span class="brand__mark"></span>
      <div class="brand__text">
        <span class="brand__name">1876 Basins &amp; Spouts</span>
        <span class="brand__tagline">Classic fixtures made for the way you live today</span>
      </div>
    </div>
    <p class="front__web">www.1876basinsandspouts.com.au</p>
  </section>

  <section class="card card--back">
    <h1 class="holder">Harold Vesk</h1>
    <span class="divider"></span>
    <ul class="contacts">
      <li>
        <svg viewBox="0 0 24 24" aria-hidden="true"><path d="M6.6 10.8a15 15 0 0 0 6.6 6.6l2.2-2.2a1 1 0 0 1 1-.25 11.4 11.4 0 0 0 3.6.57 1 1 0 0 1 1 1V20a1 1 0 0 1-1 1A17 17 0 0 1 3 4a1 1 0 0 1 1-1h3.5a1 1 0 0 1 1 1c0 1.25.2 2.45.57 3.57a1 1 0 0 1-.25 1z"/></svg>
        02 7481 3926
      </li>
      <li>
        <svg viewBox="0 0 24 24" aria-hidden="true"><path d="M7 1h10a2 2 0 0 1 2 2v18a2 2 0 0 1-2 2H7a2 2 0 0 1-2-2V3a2 2 0 0 1 2-2zm0 3v15h10V4z"/></svg>
        0438 260 947
      </li>
      <li>
        <svg viewBox="0 0 24 24" aria-hidden="true"><path d="M2 5h20v14H2zm2 2v.5l8 5 8-5V7zm0 2.8V17h16V9.8l-8 5z"/></svg>
        harold@1876basinsandspouts.com.au
      </li>
      <li>
        <svg viewBox="0 0 24 24" aria-hidden="true"><path d="M12 2a10 10 0 1 0 0 20 10 10 0 0 0 0-20zm-1 17.9A8 8 0 0 1 4.1 10L9 15v1a2 2 0 0 0 2 2zm6.9-2.5A2 2 0 0 0 16 16h-1v-3a1 1 0 0 0-1-1H8v-2h2a1 1 0 0 0 1-1V7h2a2 2 0 0 0 2-2v-.4a8 8 0 0 1 2.9 12.8z"/></svg>
        www.1876basinsandspouts.com.au
      </li>
    </ul>
  </section>
</body>
</html>
```